Webdesign für Hersteller für Pack- und Palettieranlagen für den Getränke- und Lebensmittelbereich
Webdesign für Hersteller für Pack- und Palettieranlagen für den Getränke- und Lebensmittelbere..
Zielgruppe
Hersteller für Pack- und Palettieranlagen für den Getränke- und Lebensmittelbereich
Zielgruppe: Getränke- und Lebensmittelhersteller
Aufgabenstellung
die zukünftige Seite soll dynamischer und intuitiver werden
klare Strukturen, aber morderner als das jetztige Layout
Keine Kopie der alten Seite www.kolmatech.de!
Startseite soll aufgeräumter sein
Logo, Rufnummer, Mail, Social Media
Startseite mit großem Headerbild (Slider)

```html
<!DOCTYPE html>
<html lang="de">
<head>
<meta charset="utf-8">
<title>KOLMATECH Maschinenbau GmbH</title>
<link href="https://fonts.googleapis.com/css2?family=Montserrat:wght@400;500;600;700;800&display=swap" rel="stylesheet">
<style>
:root{
  --green:#5cb531;--green-dark:#4a9a26;--orange:#f08a24;--dark:#34373c;--darker:#2a2c30;
  --light:#e7f1df;--text:#333;--white:#fff;
}
*{margin:0;padding:0;box-sizing:border-box}
html,body{width:1200px;height:3733px;overflow:hidden}
body{font-family:'Montserrat',sans-serif;color:var(--text);background:#fff;position:relative}
.abs{position:absolute}
section,header,footer,nav{position:absolute;left:0;width:1200px}
/* header */
.topbar{top:0;height:84px;background:linear-gradient(90deg,#6f7a82,#8d979e 60%,#7c868d)}
.brand{position:absolute}
.brand .name{font-weight:800;font-size:38px;color:var(--green);line-height:1;letter-spacing:1px}
.brand .sub{font-size:14px;font-weight:600;color:#2b2b2b;margin-top:2px}
.contact-top{position:absolute;top:36px;color:#fff;font-size:13px;display:flex;align-items:center;gap:8px}
.btn-kontakt{position:absolute;left:1044px;top:30px;width:86px;height:32px;background:var(--green);color:#fff;font-weight:700;font-size:13px;display:flex;align-items:center;justify-content:center}
.mainnav{top:84px;height:54px;background:var(--green);display:flex;padding-left:84px}
.mainnav a{color:#fff;font-weight:600;font-size:14px;text-decoration:none;padding:0 14px;display:flex;align-items:center}
.mainnav a.active{background:#fff;color:var(--green);padding:0 14px}
/* hero */
.hero{top:138px;height:608px;background:linear-gradient(135deg,#9fb3bc,#6e8590 45%,#a8bac0 80%,#7d8f96)}
.hero-box{left:0;top:108px;width:738px;height:358px;background:rgba(50,52,55,.82)}
.hero h1{position:absolute;left:107px;top:145px;color:#fff;font-size:31px;font-weight:700;line-height:1.5;letter-spacing:.5px}
.hero h1 span{color:var(--green);font-size:40px;font-weight:800}
.hero p{position:absolute;left:109px;top:265px;width:560px;color:#fff;font-size:21px;line-height:1.25}
.btn{background:var(--green);color:#fff;font-weight:700;display:flex;align-items:center;justify-content:center;border:2px solid var(--green-dark)}
.hero .btn{position:absolute;left:107px;top:385px;width:158px;height:58px;font-size:20px}
.dots{position:absolute;display:flex;gap:22px}
.dots i{width:15px;height:15px;border-radius:50%;background:#fff;display:block}
.dots i.on{background:var(--green)}
.badge{position:absolute;width:82px;height:116px;background:#1e3f9a;border:2px solid #fff}
/* products */
.products{top:804px;height:373px;background:linear-gradient(180deg,#303236,#45484c)}
.sec-title{font-weight:800;color:var(--orange);letter-spacing:1px}
.products .accent{left:0;top:68px;width:60px;height:245px;background:var(--green)}
.products h2{position:absolute;left:100px;top:60px;font-size:40px;line-height:1.3}
.products h2 .ul{border-bottom:5px solid #fff}
.products p{position:absolute;left:100px;top:186px;width:290px;color:#fff;font-size:16px;line-height:1.3}
.arrow{position:absolute;top:280px;width:32px;height:32px;background:var(--green);display:flex;align-items:center;justify-content:center}
.pcard{position:absolute;top:68px;height:245px;overflow:hidden;color:#fff;text-align:center}
.pcard h3{font-size:20px;font-weight:800;margin-top:108px}
.pcard small{font-size:12px;display:block;margin-top:4px}
.pcard .more{display:inline-block;margin-top:32px;border:2px solid #fff;padding:8px 10px;font-size:13px;font-weight:700}
/* about */
.about{top:1232px;height:533px}
.about h2{position:absolute;left:100px;top:10px;font-size:40px}
.about .rule{left:100px;top:74px;width:240px;height:5px;background:var(--text)}
.about p{position:absolute;left:96px;top:100px;width:510px;font-size:17px;line-height:1.25}
.stat{position:absolute;left:96px;width:504px;height:64px;background:var(--dark);border:3px dashed var(--green);display:flex;align-items:center;color:#fff}
.stat .ic{width:38px;height:38px;border-radius:50%;background:var(--green);margin:0 18px 0 36px}
.stat b{font-size:27px;font-weight:800;width:150px}
.stat b small{font-size:15px;color:var(--green)}
.stat em{font-style:normal;font-weight:700;font-size:15px;margin-left:auto;margin-right:18px}
.about .btn{position:absolute;left:96px;top:474px;width:504px;height:59px;font-size:20px}
.about-img{left:672px;top:25px;width:528px;height:508px;background:linear-gradient(160deg,#4e6672,#7f97a0 50%,#3f545d)}
/* news */
.news{top:1823px;height:582px;background:linear-gradient(180deg,#2f3134,#44474b)}
.news h2{position:absolute;left:0;width:1200px;text-align:center;top:40px;font-size:40px}
.news p{position:absolute;left:80px;width:1040px;text-align:center;top:103px;color:#fff;font-size:16px;line-height:1.3}
.ncard{position:absolute;top:177px;height:310px;overflow:hidden}
.ncard .img{position:absolute;left:0;top:0;width:100%;height:230px}
.ncard .cap{position:absolute;left:0;bottom:0;width:100%;height:80px;background:var(--green);color:#fff;font-size:17px;font-weight:500;display:flex;align-items:center;justify-content:center;text-align:center;line-height:1.25;padding:0 12px}
.ncard.feature{background:rgba(92,181,49,.88);color:#fff;text-align:center}
.ncard.feature .t{margin:36px 28px 0;font-size:18px;line-height:1.2}
.ncard.feature .b{margin:26px auto 0;width:254px;height:56px;border:3px solid #fff;font-weight:700;font-size:17px;display:flex;align-items:center;justify-content:center}
.ndots{position:absolute;left:496px;top:528px;display:flex;gap:22px}
.ndots i{width:14px;height:14px;border-radius:50%;background:#fff;display:block}
.ndots i.off{background:none;border:2px solid #fff}
/* jobs */
.jobs{top:2463px;height:508px}
.jobs .block{left:74px;top:0;width:419px;height:487px;background:var(--green)}
.jobs .video{left:119px;top:67px;width:496px;height:376px;background:linear-gradient(160deg,#5b6066,#8a8274 50%,#3d5080)}
.play{position:absolute;left:225px;top:160px;width:54px;height:54px;border-radius:50%;background:#fff}
.jobs h2{position:absolute;left:670px;top:60px;font-size:40px}
.jobs .rule{left:670px;top:122px;width:200px;height:5px;background:var(--text)}
.jobs p{position:absolute;left:670px;top:148px;width:470px;font-size:17px;line-height:1.55}
.jobs .btn{position:absolute;left:667px;top:352px;width:458px;height:70px;font-size:16px;border:3px solid #fff;box-shadow:0 0 0 2px var(--green)}
/* contact */
.contact{top:2971px;height:420px}
.contact h2{position:absolute;left:100px;top:66px;font-size:40px}
.contact .lead{position:absolute;left:98px;top:136px;font-size:20px}
.citem{position:absolute;display:flex;gap:18px}
.citem .ci{width:44px;height:44px;border-radius:50%;background:var(--green);flex:none;margin-top:8px;display:flex;align-items:center;justify-content:center}
.citem span{font-size:17px;display:block;color:#444}
.citem strong{font-size:17px;font-weight:600;display:block;line-height:1.25;color:#222}
.citem .addr{width:200px}
.map{left:692px;top:67px;width:404px;height:302px;background:linear-gradient(135deg,#e9e9e7,#dcdcd9);border:1px solid #ccc}
/* footer */
.footer{top:3398px;height:335px;background:#fff}
.f-top{left:0;top:0;width:1200px;height:86px;background:var(--light);border-bottom:4px solid #6f6f6f}
.f-col{position:absolute;font-size:14px;line-height:1.8;color:#444}
.f-col h4{font-size:13px;font-weight:700;color:#222;margin-bottom:8px}
.social{position:absolute;left:133px;top:222px;display:flex;gap:23px}
.social i{width:38px;height:38px;background:var(--orange);display:block}
.f-bottom{left:0;top:296px;width:1200px;height:39px;border-top:4px solid #6f6f6f;display:flex;gap:60px;align-items:center;justify-content:center;color:var(--green);font-size:14px;font-weight:500}
</style>
</head>
<body>

<header class="topbar">
  <div class="brand" style="left:100px;top:14px">
    <div class="name">KOLMATECH</div><div class="sub">Maschinenbau GmbH</div>
  </div>
  <div class="contact-top" style="left:722px">
    <svg width="18" height="18" viewBox="0 0 24 24"><path fill="#fff" d="M6.6 10.8a15.1 15.1 0 0 0 6.6 6.6l2.2-2.2c.3-.3.7-.4 1-.2 1.1.4 2.3.6 3.6.6.6 0 1 .4 1 1V20c0 .6-.4 1-1 1A17 17 0 0 1 3 4c0-.6.4-1 1-1h3.5c.6 0 1 .4 1 1 0 1.3.2 2.5.6 3.6.1.3 0 .7-.2 1z"/></svg>
    03412 / 480 - 0
  </div>
  <div class="contact-top" style="left:870px">
    <svg width="24" height="16" viewBox="0 0 24 16"><rect x="1" y="1" width="22" height="14" fill="none" stroke="#fff" stroke-width="2"/><path d="M1 1l11 8 11-8" fill="none" stroke="#fff" stroke-width="2"/></svg>
    info@kolmatech.de
  </div>
  <div class="btn-kontakt">KONTAKT</div>
</header>

<nav class="mainnav">
  <a class="active">Unternehmen</a><a>Jobs &amp; Karriere</a><a>Palettiertechnik</a><a>Packertechnik</a><a>Fördertechnik</a><a>Anlagen</a><a>Gebrauchtmaschinen</a><a>Aktuelles</a>
</nav>

<section class="hero" role="img" aria-label="Abfüllhalle mit Förderband für Flaschen">
  <div class="abs hero-box"></div>
  <h1>FORTSCHRITTLICHE VERPACKUNG<br>FÜR DIE <span>MODERNE INDUSTRIE</span></h1>
  <p>Neueste Verpackungslösungen Für Hochwertige Lebensmittel Und Getränke, Effizienzsteigerung Und Ertragsoptimierung</p>
  <div class="btn">MEHR</div>
  <div class="dots" style="left:146px;top:523px"><i></i><i></i><i></i><i class="on"></i><i></i><i></i></div>
  <div class="badge" style="left:946px;top:425px"></div>
  <div class="badge" style="left:1038px;top:425px"></div>
</section>

<section class="products">
  <div class="abs accent"></div>
  <h2 class="sec-title">UNSERE<br><span class="ul">PRODUKTE</span></h2>
  <p>Erfahren Sie Mehr Über Unsere Produkte. Wählen Sie Eine Kategorie:</p>
  <div class="arrow" style="left:331px"><svg width="14" height="16"><path d="M13 0L0 8l13 8z" fill="#fff"/></svg></div>
  <div class="arrow" style="left:377px"><svg width="14" height="16"><path d="M1 0l13 8-13 8z" fill="#fff"/></svg></div>
  <div class="pcard" style="left:430px;width:308px;background:linear-gradient(180deg,#6f8fb0,#2e4a78 60%,#c87a2a)" role="img" aria-label="Fördertechnik mit Flaschentransport">
    <h3 style="color:var(--green);margin-top:96px">FÖRDERTECHNIK</h3><small>FlowTrans Behälter- Und Gebindetransport</small>
  </div>
  <div class="pcard" style="left:768px;width:308px;background:rgba(92,181,49,.85)" role="img" aria-label="Packertechnik Maschine">
    <h3 style="margin-top:36px">PACKERTECHNIK</h3><small>FlowPac Unsere Flaschenpacker</small>
    <span class="more">MEHR DAZU</span>
  </div>
  <div class="pcard" style="left:1108px;width:92px;background:linear-gradient(180deg,#8fa4b4,#c9b08a)" role="img" aria-label="Palettiertechnik">
    <h3 style="color:var(--green);text-align:left;padding-left:40px;white-space:nowrap;margin-top:100px">PALETTIER</h3><small style="text-align:left;padding-left:16px;white-space:nowrap">FlowPal Unsere</small>
  </div>
</section>

<section class="about">
  <h2 class="sec-title">UBER UNS</h2>
  <div class="abs rule"></div>
  <p>Das Traditionsreiche Familienunternehmen Kolmatech Plant, Entwickelt Und Baut Pack- Und Palettieranlagen Für Den Getränke- Und Lebensmittelbereich. Mit Erfahrung Und Know-How Planen Und Konstruieren Wir Moderne Und Effiziente Anlagen,</p>
  <div class="stat" style="top:230px"><span class="ic"></span><b>155 <small>Jahr</small></b><em>QUALITÄT UND ERFAHRUNG</em></div>
  <div class="stat" style="top:305px"><span class="ic"></span><b>2500 <small>M²</small></b><em>PRODUKTIONSRAUM</em></div>
  <div class="stat" style="top:380px"><span class="ic"></span><b>350 <small>+</small></b><em>PRODUKTIONSRAUM</em></div>
  <div class="btn">MEHR</div>
  <div class="abs about-img" role="img" aria-label="Moderne Fertigungshalle mit CAD-Arbeitsplatz"></div>
</section>

<section class="news">
  <h2 class="sec-title">AKTUELLES</h2>
  <p>Lorem Ipsum Is Simply Dummy Text Of The Printing And Typesetting Industry. Lorem Ipsum Has Been The Industry's Standard Dummy Text Ever Since The 1500s</p>
  <div class="ncard" style="left:0;width:84px"><div class="img" role="img" aria-label="Produktionsanlage" style="background:linear-gradient(160deg,#9aa6b0,#5b7a4a)"></div><div class="cap" style="justify-content:flex-start;padding:0 4px">kenteil</div></div>
  <div class="ncard" style="left:106px;width:314px"><div class="img" role="img" aria-label="Mitarbeiter an Glasabfüllanlage" style="background:linear-gradient(160deg,#c9ccc9,#6d7a70 60%,#3b4a44)"></div><div class="cap">Erneuerung Glasabfüllanlage Molkerei Talgrund</div></div>
  <div class="ncard" style="left:437px;width:314px"><div class="img" role="img" aria-label="Grüne Flaschen in Abfüllanlage" style="background:linear-gradient(160deg,#8a9096,#3a4a3a 55%,#5ab43a)"></div><div class="cap">Neue Abfüllanlage Für Brunnhof Limo</div></div>
  <div class="ncard feature" style="left:773px;width:314px"><div class="t">Neue Abfüllanlage Für Die Auenhofer Süßmost-, Weinkelterei &amp; Edeldestille GmbH</div><div class="b">LESEN SIE MEHR DAZU</div></div>
  <div class="ncard" style="left:1114px;width:86px"><div class="img" role="img" aria-label="Verpackungsanlage" style="background:linear-gradient(160deg,#e4e4e4,#c05050)"></div><div class="cap" style="justify-content:flex-start;padding:0 4px">Neue</div></div>
  <div class="ndots"><i></i><i></i><i></i><i class="off"></i><i></i><i></i></div>
</section>

<section class="jobs">
  <div class="abs block"></div>
  <div class="abs video" role="img" aria-label="Videovorschau mit Mitarbeitern in Arbeitskleidung">
    <div class="play"><svg width="54" height="54"><path d="M22 16l16 11-16 11z" fill="var(--green)"/></svg></div>
  </div>
  <h2 class="sec-title">JOBS UND KARRIERE</h2>
  <div class="abs rule"></div>
  <p>Schauen Sie sich jetzt unsere aktuellen Stellenangebote an und bewerben Sie sich ganz einfach auf Ihre Wunschstelle. Eine Bewerbung läuft ganz einfach in 60 Sekunden ab – ohne Lebenslauf oder Anschreiben.</p>
  <div class="btn">JETZT STELLEN ANSEHEN UND BEWERBEN</div>
</section>

<section class="contact">
  <h2 class="sec-title">KONTAKT</h2>
  <div class="lead">Kontaktieren Sie Uns Hier, Wenn Sie Fragen Haben</div>
  <div class="citem" style="left:108px;top:204px"><div class="ci"><svg width="20" height="24" viewBox="0 0 20 24"><path d="M10 1a8 8 0 0 0-8 8c0 6 8 14 8 14s8-8 8-14a8 8 0 0 0-8-8z" fill="none" stroke="#fff" stroke-width="2"/><circle cx="10" cy="9" r="3" fill="#fff"/></svg></div><div class="addr"><span>Standort</span><strong>KOLMATECH<br>Maschinenbau GmbH<br>Am Werkhof 12<br>04720 Lindenau</strong></div></div>
  <div class="citem" style="left:402px;top:204px"><div class="ci"><svg width="20" height="14"><rect x="1" y="1" width="18" height="12" fill="none" stroke="#fff" stroke-width="2"/><path d="M1 1l9 7 9-7" fill="none" stroke="#fff" stroke-width="2"/></svg></div><div><span>Email</span><strong>Info@Kolmatech.De</strong></div></div>
  <div class="citem" style="left:108px;top:320px"><div class="ci"><svg width="20" height="20" viewBox="0 0 24 24"><path fill="#fff" d="M6.6 10.8a15.1 15.1 0 0 0 6.6 6.6l2.2-2.2c.3-.3.7-.4 1-.2 1.1.4 2.3.6 3.6.6.6 0 1 .4 1 1V20c0 .6-.4 1-1 1A17 17 0 0 1 3 4c0-.6.4-1 1-1h3.5c.6 0 1 .4 1 1 0 1.3.2 2.5.6 3.6.1.3 0 .7-.2 1z"/></svg></div><div><span>Telefon</span><strong style="font-weight:500">03412 / 480 - 0</strong></div></div>
  <div class="citem" style="left:402px;top:320px"><div class="ci"><svg width="20" height="20"><rect x="3" y="7" width="14" height="10" fill="#fff"/><rect x="6" y="2" width="8" height="6" fill="none" stroke="#fff" stroke-width="2"/></svg></div><div><span>Fax</span><strong style="font-weight:500">03412 / 480 - 0</strong></div></div>
  <div class="abs map" role="img" aria-label="Lagekarte des Firmenstandorts"></div>
</section>

<footer class="footer">
  <div class="abs f-top"></div>
  <div class="brand" style="left:130px;top:16px">
    <div class="name">KOLMATECH</div><div class="sub" style="font-size:16px">Maschinenbau GmbH</div>
  </div>
  <div class="abs" style="left:788px;top:30px;width:170px;height:50px;background:#1e3f9a"></div>
  <div class="abs" style="left:970px;top:30px;width:118px;height:50px;background:#fff;border:2px solid #1e3f9a"></div>
  <div class="f-col" style="left:133px;top:98px;width:240px;font-size:12px;line-height:1.45">Fortschrittliche Verpackung Für Die Moderne Industrie,Neueste Verpackungslösungen Für Hochwertige Lebensmittel Und Getränke.
    <div style="font-size:17px;font-weight:600;color:#222;margin-top:12px">Folgen Sie Uns</div></div>
  <div class="social"><i></i><i></i><i></i><i></i></div>
  <div class="f-col" style="left:455px;top:112px"><h4>QUICKLINKS</h4>Startseite<br>Unternehmen<br>Downloads<br>Medien-Center<br>Presse</div>
  <div class="f-col" style="left:642px;top:112px"><h4>PRODUKTE</h4>Palettiertechnik<br>Packertechnik<br>Fördertechnik<br>Anlagen<br>Gebrauchtmaschinen</div>
  <div class="f-col" style="left:840px;top:112px;line-height:1.35"><h4>KONTAKT</h4>KOLMATECH Maschinenbau GmbH<br>Am Werkhof 12<br>04720 Lindenau<br><br>Telefon &nbsp;&nbsp;&nbsp;&nbsp;: 03412 / 480 - 0<br>Fax &nbsp;&nbsp;&nbsp;&nbsp;&nbsp;&nbsp;&nbsp;&nbsp;&nbsp;&nbsp;: 03412 / 480 - 14<br>E-Mail &nbsp;&nbsp;&nbsp;&nbsp;&nbsp;: Info@Kolmatech.De</div>
  <div class="abs f-bottom"><span>2024 © KOLMATECH Maschinenbau GmbH</span><span>Datenschutz &nbsp;&nbsp;&nbsp; Impressum</span></div>
</footer>

</body>
</html>
```